Redesign 2016 Digital Marketing Website and Convert to Wordpress

Technology needed to integrate:

- redesign and convert to wordpress
- gravity forms
- malware and hacker defense / honeypot (must be very secure from hackers)
- I want gravity forms to be a flow that asks many questions with icons and progress bar.
- 1 home page design
- 1 blog design
- 1 design for internal page content
- 1 multi step gravity form
I want to focus on SMB's. We are a marketing agency thats been around since 2016.

Site is: tallpine.agency

I am looking to redesign the homepage, blog page and services page. The services page will be a template for all inner pages of the site. All content needs to be moved into the new design.

I want to get ride of the weird video.

I need you to install gravity forms pro model so we can pass utms.

I need the gravity form to be a multi step form with icons.

All "contact us" or "get a free assesments" call to actions will go to this form only.

step 1:
what is your website

step 2:
what industry are you in
- option
- Home Services
- Legal
- Ecommerce
- Lead Gen

No matter which one they select its going to produce a differnt calculator for them.

Law:
How many leads did you get last month
how much is each ase worth on average
How much revenue do you want to make

Home servicse:
How many bookings did you get last month
How much is each service worht on average
How much revenue do you wangt to make

Ecommerce:
What is your average order value
How muny purchases did you have last month
How much revenue did you drive
How much revenue do you want to drive

For lead gen:
How many leads did you get lawt month
How much revenue did they generate

Step 3:
What is your current advertising budget

step 4:
Do you have a CRM and if so what is it

Step 5:
What is your personal informagtion
name
email
phone

Let me know if this is enough to get you going

Small and medium sized law firms, ecommerce, home services and lead gen customers.

We are a digital marketing agency

• Use whats on the current site and improve upon it

• Must be very secure, developed into a wordpress website. using gravity forms. remove my photo and my staffs photo, depersonalize it so it doesnt mention me or sam crolley. Use the same color scheme. I am looking to redesign the homepage, blog page and services page. The services page will be a template for all inner pages of the site. All content needs to be moved into the new design. I want to get ride of the weird video. I need you to install gravity forms pro model so we can pass utms. I need the gravity form to be a multi step form with icons. All "contact us" or "get a free assesments" call to actions will go to this form only. step 1: what is your website step 2: what industry are you in - option - Home Services - Legal - Ecommerce - Lead Gen No matter which one they select its going to produce a differnt calculator for them. Law: How many leads did you get last month how much is each ase worth on average How much revenue do you want to make Home servicse: How many bookings did you get last month How much is each service worht on average How much revenue do you wangt to make Ecommerce: What is your average order value How muny purchases did you have last month How much revenue did you drive How much revenue do you want to drive For lead gen: How many leads did you get lawt month How much revenue did they generate How much revenue do you want to make Step 3: What is your current advertising budget step 4: Do you have a CRM and if so what is it Step 5: What is your personal informagtion name email phone Let me know if this is enough to get you going
• SHOULD NOT BE SLOPPY, I AM LOOKING FOR ATTENTION TO DETAIL.

```html
<!DOCTYPE html>
<html lang="en">
<head>
<meta charset="utf-8">
<title>Tall Pine – Free Assessment Multi-Step Form</title>
<link href="https://fonts.googleapis.com/css2?family=Montserrat:wght@400;500;600;700;800&display=swap" rel="stylesheet">
<style>
:root{
  --board:#a2a2a2;
  --brand-red:#7a1315;
  --title-red:#7b1a1b;
  --ink:#222222;
  --muted:#6a6a6a;
  --soft:#f3f3f3;
  --line:#dcdcdc;
  --dot:#c6c6c6;
  --white:#ffffff;
  --pill-gray:#9b9b9b;
  --hero-dark:#171415;
  --hero-mid:#3a3839;
}
*{box-sizing:border-box;margin:0;padding:0}
html,body{width:1200px;height:1167px;overflow:hidden}
body{background:var(--board);font-family:"Montserrat",Arial,sans-serif;color:var(--ink)}
.board{position:relative;width:1200px;height:1167px}

/* board titles */
.step-title{position:absolute;transform:translateX(-50%);font-size:38px;line-height:38px;font-weight:800;color:var(--title-red);letter-spacing:.5px;white-space:nowrap}
.step-title--1{left:240px;top:10px}
.step-title--2{left:591px;top:10px}
.step-title--3{left:950px;top:10px}
.step-title--4{left:236px;top:612px}
.step-title--5{left:579px;top:612px}
.board-note{position:absolute;left:805px;top:777px;width:380px;text-align:center;font-size:38px;line-height:39.5px;font-weight:800;color:var(--white)}

/* page mockup */
.page{position:absolute;width:341px;background:var(--white);display:flex;flex-direction:column;overflow:hidden}
.page--1{left:70px;top:56px;height:492px}
.page--2{left:430px;top:55px;height:535px}
.page--3{left:794px;top:55px;height:481px}
.page--4{left:70px;top:656px;height:481px}
.page--5{left:430px;top:656px;height:481px}

/* header */
.site-header{position:relative;height:19px;flex:none;display:flex;align-items:center;background:var(--white)}
.brand{display:flex;align-items:center;gap:3px;margin-left:28px}
.brand-dot{width:15px;height:15px;border-radius:50%;background:var(--brand-red)}
.brand-name{font-size:6.5px;font-weight:400;color:#5a5a5a;letter-spacing:.6px}
.site-nav{display:flex;gap:10px;margin-left:17px}
.site-nav a{font-size:3.6px;font-weight:600;color:var(--ink);text-decoration:none;letter-spacing:.1px}
.site-nav a.is-current{border-bottom:.6px solid var(--brand-red);padding-bottom:1px;color:var(--brand-red)}
.header-cta{position:absolute;right:0;top:0;height:19px;width:62px;background:var(--brand-red);clip-path:polygon(6px 0,100% 0,100% 100%,0 100%);color:var(--white);padding:4px 0 0 10px}
.header-cta strong{display:block;font-size:3.3px;font-weight:700;line-height:4.4px}
.header-cta span{display:block;font-size:2.8px;font-weight:400;line-height:3.6px}

/* hero */
.hero{position:relative;height:120px;flex:none;text-align:center;color:var(--white)}
.hero-backdrop{position:absolute;inset:0;background:
  radial-gradient(ellipse 70% 40% at 55% 72%,rgba(120,118,120,.45),rgba(0,0,0,0) 70%),
  linear-gradient(180deg,var(--hero-dark) 0%,#221f20 55%,var(--hero-mid) 100%)}
.hero-copy{position:relative;padding-top:41px}
.hero-kicker{font-size:6.6px;font-weight:400;letter-spacing:.2px}
.hero-heading{font-size:12.6px;font-weight:500;letter-spacing:.3px;margin-top:1px}

/* form section */
.form-section{position:relative;flex:none;background:var(--soft);height:183px}
.page--2 .form-section{height:233px}
.page--3 .form-section,.page--4 .form-section,.page--5 .form-section{height:184px}
.progress{position:absolute;left:0;top:0;width:100%;height:40px}
.progress-track{position:absolute;left:87px;width:167px;top:23px;height:.6px;background:var(--dot)}
.progress-step{position:absolute;top:21px;width:30px;margin-left:-15px;text-align:center}
.progress-step::before{content:"";display:block;width:4px;height:4px;margin:0 auto;border-radius:50%;background:var(--dot);box-shadow:0 0 0 3px var(--soft)}
.progress-step.is-active::before{background:var(--brand-red)}
.progress-step span{display:block;margin-top:5px;font-size:4.4px;font-weight:700;color:var(--brand-red)}
.progress-step:nth-child(2){left:87px}
.progress-step:nth-child(3){left:127px}
.progress-step:nth-child(4){left:170px}
.progress-step:nth-child(5){left:209px}
.progress-step:nth-child(6){left:254px}

.form-card{position:absolute;top:50px;left:50%;transform:translateX(-50%);background:var(--white);border:.6px solid #e2c9c9;border-radius:3px;box-shadow:0 0 3px rgba(0,0,0,.08);text-align:center}
.form-card--url{width:207px;height:91px}
.form-card--industry{width:224px;height:152px}
.form-card--budget{width:224px;height:93px}
.form-card--crm{width:224px;height:98px}
.form-card--contact{width:230px;height:92px}
.form-card h3{font-size:6.4px;font-weight:700;color:var(--brand-red);margin-top:19px}
.form-card--industry h3{margin-top:15px}
.text-field{height:15px;border:.6px solid #b9b9b9;background:var(--white);font-size:3.6px;color:#707070;text-align:left;padding:5px 0 0 7px}
.form-card .text-field--wide{width:140px;margin:6px auto 0}
.btn-next{display:inline-flex;align-items:center;gap:2px;justify-content:center;height:14px;width:45px;border-radius:7px;background:var(--brand-red);color:var(--white);font-size:4.2px;font-weight:700;margin-top:7px}
.btn-next svg{width:7px;height:4px}

/* industry options */
.industry-options{display:flex;gap:5px;margin:11px 0 0 21px}
.industry-option{width:42px;height:30px;border:.6px solid #d7d7d7;border-radius:2px;display:flex;flex-direction:column;align-items:center;justify-content:center;gap:2px;color:#444;font-size:3.5px;font-weight:600}
.industry-option svg{width:11px;height:11px}
.industry-option.is-selected{background:var(--brand-red);border-color:var(--brand-red);color:var(--white)}
.calc-fields{display:grid;grid-template-columns:90px 90px;column-gap:3px;row-gap:5px;margin:14px 0 0 23px;text-align:left}
.calc-field label{display:block;font-size:3.2px;font-weight:600;color:#333;margin-bottom:3px}
.calc-field .text-field{height:9px;padding:0}
.form-card--industry .btn-next{margin-top:9px}

/* contact row */
.contact-fields{display:flex;gap:3px;margin:9px 0 0 18px}
.contact-fields .text-field{width:65px;height:14px;padding-top:4.5px}

/* footer */
.footer-cta{flex:none;height:30px;display:flex;align-items:center;border-bottom:.6px solid var(--line);padding-left:40px}
.footer-cta .brand{margin-left:0}
.footer-cta .brand-dot{width:16px;height:16px}
.footer-cta .brand-name{font-size:6.6px}
.footer-buttons{display:flex;gap:8px;margin-left:auto;margin-right:40px}
.pill{height:13px;border-radius:7px;display:flex;align-items:center;justify-content:center;font-size:3.3px;font-weight:700;color:var(--white);letter-spacing:.1px}
.pill--call{width:61px;background:var(--pill-gray)}
.pill--grow{width:61px;background:var(--brand-red)}
.footer-links{flex:1;display:grid;grid-template-columns:64px 81px 72px auto;padding:13px 0 0 42px}
.footer-col h4{font-size:4.3px;font-weight:700;color:var(--ink);border-left:1px solid var(--brand-red);padding-left:3px;line-height:5px}
.footer-col ul{list-style:none;margin:3px 0 0 4px}
.footer-col li{font-size:3.2px;line-height:6.6px;color:var(--muted)}
.footer-copy{flex:none;height:27px;border-top:.6px solid var(--line);display:flex;align-items:center;justify-content:center;font-size:3px;color:var(--muted)}
</style>
</head>
<body>
<main class="board">

  <h2 class="step-title step-title--1">STEP 1</h2>
  <h2 class="step-title step-title--2">STEP 2</h2>
  <h2 class="step-title step-title--3">STEP 3</h2>
  <h2 class="step-title step-title--4">STEP 4</h2>
  <h2 class="step-title step-title--5">STEP 5</h2>

  <p class="board-note">ALL THESE 5 STEPS WILL BE ON THE SAME PAGE</p>

  <!-- ===== Step 1: website ===== -->
  <article class="page page--1">
    <header class="site-header">
      <div class="brand"><span class="brand-dot"></span><span class="brand-name">TALL PINE</span></div>
      <nav class="site-nav"><a>ABOUT</a><a>INDUSTRIES</a><a>SERVICES</a><a class="is-current">BLOG</a><a>CONTACT US</a></nav>
      <div class="header-cta"><strong>GET A FREE CONSULTATION</strong><span>OR CAL US (555) 014-2290</span></div>
    </header>
    <section class="hero">
      <div class="hero-backdrop" role="img" aria-label="Dark abstract backdrop of a glowing network mesh wave"></div>
      <div class="hero-copy"><p class="hero-kicker">CONTACT US NOW</p><h1 class="hero-heading">GET A FREE ASSESMENTS</h1></div>
    </section>
    <section class="form-section">
      <div class="progress">
        <div class="progress-track"></div>
        <div class="progress-step is-active"><span>STEP 1</span></div>
        <div class="progress-step"><span>STEP 2</span></div>
        <div class="progress-step"><span>STEP 3</span></div>
        <div class="progress-step"><span>STEP 4</span></div>
        <div class="progress-step"><span>STEP 5</span></div>
      </div>
      <div class="form-card form-card--url">
        <h3>What is your website ?</h3>
        <div class="text-field text-field--wide">Your Website link</div>
        <div class="btn-next">NEXT <svg viewBox="0 0 14 8" fill="none" stroke="currentColor" stroke-width="1.2"><path d="M0 4h12M9 1l3 3-3 3"/></svg></div>
      </div>
    </section>
    <div class="footer-cta">
      <div class="brand"><span class="brand-dot"></span><span class="brand-name">TALL PINE</span></div>
      <div class="footer-buttons"><span class="pill pill--call">CALL US (555) 014-2290</span><span class="pill pill--grow">GROW YOUR REVENUE</span></div>
    </div>
    <div class="footer-links">
      <div class="footer-col"><h4>QUICK LINKS</h4><ul><li>About</li><li>Industries</li><li>Training</li><li>Blog</li><li>Services</li><li>Contact</li></ul></div>
      <div class="footer-col"><h4>SERVICES</h4><ul><li>Programmatic Advertising</li><li>Search Engine Marketing (SEM)</li><li>Search Engine Optimization (SEO)</li><li>Content Marketing</li><li>Email Marketing</li><li>Paid Search Advertising</li><li>Paid Social Advertising</li></ul></div>
      <div class="footer-col"><h4>INDUSTRIES</h4><ul><li>Ecommerce</li><li>Electricians</li><li>Financial Services Marketing</li><li>Home Builders</li><li>Home Services</li><li>Hvac Companies</li><li>Cosmetic Surgery Centers</li><li>Dental Marketing</li><li>Education</li><li>Healthcare Medical Marketing</li><li>Plumbing Companies</li><li>Podiatrist Marketing</li><li>Landscapers</li></ul></div>
      <div class="footer-col"><h4>LINKS</h4><ul><li>Training</li><li>Resources</li><li>Privacy Policy</li><li>Sitemap</li><li>Terms Of Use</li><li>Press &amp; Media</li><li>Cookie Policy</li></ul></div>
    </div>
    <div class="footer-copy">© 2024 Company Name | All Rights Reserved</div>
  </article>

  <!-- ===== Step 2: industry ===== -->
  <article class="page page--2">
    <header class="site-header">
      <div class="brand"><span class="brand-dot"></span><span class="brand-name">TALL PINE</span></div>
      <nav class="site-nav"><a>ABOUT</a><a>INDUSTRIES</a><a>SERVICES</a><a>BLOG</a><a>CONTACT US</a></nav>
      <div class="header-cta"><strong>GET A FREE CONSULTATION</strong><span>OR CAL US (555) 014-2290</span></div>
    </header>
    <section class="hero">
      <div class="hero-backdrop" role="img" aria-label="Dark abstract backdrop of a glowing network mesh wave"></div>
      <div class="hero-copy"><p class="hero-kicker">CONTACT US NOW</p><h1 class="hero-heading">GET A FREE ASSESMENTS</h1></div>
    </section>
    <section class="form-section">
      <div class="progress">
        <div class="progress-track"></div>
        <div class="progress-step"><span>STEP 1</span></div>
        <div class="progress-step is-active"><span>STEP 2</span></div>
        <div class="progress-step"><span>STEP 3</span></div>
        <div class="progress-step"><span>STEP 4</span></div>
        <div class="progress-step"><span>STEP 5</span></div>
      </div>
      <div class="form-card form-card--industry">
        <h3>What Industry are you in</h3>
        <div class="industry-options">
          <div class="industry-option is-selected">
            <svg viewBox="0 0 24 24" fill="none" stroke="currentColor" stroke-width="1.4"><path d="M3 21h18M5 21V6l7-3 7 3v15"/><path d="M9 9h2v2H9zM13 9h2v2h-2zM9 13h2v2H9zM13 13h2v2h-2zM10 21v-3h4v3"/></svg>
            Home Services
          </div>
          <div class="industry-option">
            <svg viewBox="0 0 24 24" fill="none" stroke="currentColor" stroke-width="1.4"><path d="M12 3v17M7 21h10M4 7h16"/><path d="M6 7l-3 7a3 3 0 0 0 6 0zM18 7l-3 7a3 3 0 0 0 6 0z"/></svg>
            Legal
          </div>
          <div class="industry-option">
            <svg viewBox="0 0 24 24" fill="none" stroke="currentColor" stroke-width="1.4"><path d="M3 9h18l-2 11H5z"/><path d="M8 9l4-5 4 5M9 12v5M12 12v5M15 12v5"/></svg>
            Ecommerce
          </div>
          <div class="industry-option">
            <svg viewBox="0 0 24 24" fill="none" stroke="currentColor" stroke-width="1.4"><circle cx="15" cy="7" r="3"/><path d="M10 17a5 5 0 0 1 10 0"/><circle cx="7" cy="12" r="2.5"/><path d="M3 21a4 4 0 0 1 8 0"/></svg>
            Lead Gen
          </div>
        </div>
        <div class="calc-fields">
          <div class="calc-field"><label>How many bookings did you get last month</label><div class="text-field"></div></div>
          <div class="calc-field"><label>How much is each service worht on average</label><div class="text-field"></div></div>
          <div class="calc-field"><label>How much revenue do you want to make</label><div class="text-field"></div></div>
        </div>
        <div class="btn-next">NEXT <svg viewBox="0 0 14 8" fill="none" stroke="currentColor" stroke-width="1.2"><path d="M0 4h12M9 1l3 3-3 3"/></svg></div>
      </div>
    </section>
    <div class="footer-cta">
      <div class="brand"><span class="brand-dot"></span><span class="brand-name">TALL PINE</span></div>
      <div class="footer-buttons"><span class="pill pill--call">CALL US (555) 014-2290</span><span class="pill pill--grow">GROW YOUR REVENUE</span></div>
    </div>
    <div class="footer-links">
      <div class="footer-col"><h4>QUICK LINKS</h4><ul><li>About</li><li>Industries</li><li>Training</li><li>Blog</li><li>Services</li><li>Contact</li></ul></div>
      <div class="footer-col"><h4>SERVICES</h4><ul><li>Programmatic Advertising</li><li>Search Engine Marketing (SEM)</li><li>Search Engine Optimization (SEO)</li><li>Content Marketing</li><li>Email Marketing</li><li>Paid Search Advertising</li><li>Paid Social Advertising</li></ul></div>
      <div class="footer-col"><h4>INDUSTRIES</h4><ul><li>Ecommerce</li><li>Electricians</li><li>Financial Services Marketing</li><li>Home Builders</li><li>Home Services</li><li>Hvac Companies</li><li>Cosmetic Surgery Centers</li><li>Dental Marketing</li><li>Education</li><li>Healthcare Medical Marketing</li><li>Plumbing Companies</li><li>Podiatrist Marketing</li><li>Landscapers</li></ul></div>
      <div class="footer-col"><h4>LINKS</h4><ul><li>Training</li><li>Resources</li><li>Privacy Policy</li><li>Sitemap</li><li>Terms Of Use</li><li>Press &amp; Media</li><li>Cookie Policy</li></ul></div>
    </div>
    <div class="footer-copy">© 2024 Company Name | All Rights Reserved</div>
  </article>

  <!-- ===== Step 3: budget ===== -->
  <article class="page page--3">
    <header class="site-header">
      <div class="brand"><span class="brand-dot"></span><span class="brand-name">TALL PINE</span></div>
      <nav class="site-nav"><a>ABOUT</a><a>INDUSTRIES</a><a>SERVICES</a><a>BLOG</a><a>CONTACT US</a></nav>
      <div class="header-cta"><strong>GET A FREE CONSULTATION</strong><span>OR CAL US (555) 014-2290</span></div>
    </header>
    <section class="hero">
      <div class="hero-backdrop" role="img" aria-label="Dark abstract backdrop of a glowing network mesh wave"></div>
      <div class="hero-copy"><p class="hero-kicker">CONTACT US NOW</p><h1 class="hero-heading">GET A FREE ASSESMENTS</h1></div>
    </section>
    <section class="form-section">
      <div class="progress">
        <div class="progress-track"></div>
        <div class="progress-step"><span>STEP 1</span></div>
        <div class="progress-step"><span>STEP 2</span></div>
        <div class="progress-step is-active"><span>STEP 3</span></div>
        <div class="progress-step"><span>STEP 4</span></div>
        <div class="progress-step"><span>STEP 5</span></div>
      </div>
      <div class="form-card form-card--budget">
        <h3>What is your current advertising budget</h3>
        <div class="text-field text-field--wide">Type Current Budget</div>
        <div class="btn-next">NEXT <svg viewBox="0 0 14 8" fill="none" stroke="currentColor" stroke-width="1.2"><path d="M0 4h12M9 1l3 3-3 3"/></svg></div>
      </div>
    </section>
    <div class="footer-cta">
      <div class="brand"><span class="brand-dot"></span><span class="brand-name">TALL PINE</span></div>
      <div class="footer-buttons"><span class="pill pill--call">CALL US (555) 014-2290</span><span class="pill pill--grow">GROW YOUR REVENUE</span></div>
    </div>
    <div class="footer-links">
      <div class="footer-col"><h4>QUICK LINKS</h4><ul><li>About</li><li>Industries</li><li>Training</li><li>Blog</li><li>Services</li><li>Contact</li></ul></div>
      <div class="footer-col"><h4>SERVICES</h4><ul><li>Programmatic Advertising</li><li>Search Engine Marketing (SEM)</li><li>Search Engine Optimization (SEO)</li><li>Content Marketing</li><li>Email Marketing</li><li>Paid Search Advertising</li><li>Paid Social Advertising</li></ul></div>
      <div class="footer-col"><h4>INDUSTRIES</h4><ul><li>Ecommerce</li><li>Electricians</li><li>Financial Services Marketing</li><li>Home Builders</li><li>Home Services</li><li>Hvac Companies</li><li>Cosmetic Surgery Centers</li><li>Dental Marketing</li><li>Education</li><li>Healthcare Medical Marketing</li><li>Plumbing Companies</li><li>Podiatrist Marketing</li><li>Landscapers</li></ul></div>
      <div class="footer-col"><h4>LINKS</h4><ul><li>Training</li><li>Resources</li><li>Privacy Policy</li><li>Sitemap</li><li>Terms Of Use</li><li>Press &amp; Media</li><li>Cookie Policy</li></ul></div>
    </div>
    <div class="footer-copy">© 2024 Company Name | All Rights Reserved</div>
  </article>

  <!-- ===== Step 4: CRM ===== -->
  <article class="page page--4">
    <header class="site-header">
      <div class="brand"><span class="brand-dot"></span><span class="brand-name">TALL PINE</span></div>
      <nav class="site-nav"><a>ABOUT</a><a>INDUSTRIES</a><a>SERVICES</a><a>BLOG</a><a>CONTACT US</a></nav>
      <div class="header-cta"><strong>GET A FREE CONSULTATION</strong><span>OR CAL US (555) 014-2290</span></div>
    </header>
    <section class="hero">
      <div class="hero-backdrop" role="img" aria-label="Dark abstract backdrop of a glowing network mesh wave"></div>
      <div class="hero-copy"><p class="hero-kicker">CONTACT US NOW</p><h1 class="hero-heading">GET A FREE ASSESMENTS</h1></div>
    </section>
    <section class="form-section">
      <div class="progress">
        <div class="progress-track"></div>
        <div class="progress-step"><span>STEP 1</span></div>
        <div class="progress-step"><span>STEP 2</span></div>
        <div class="progress-step"><span>STEP 3</span></div>
        <div class="progress-step is-active"><span>STEP 4</span></div>
        <div class="progress-step"><span>STEP 5</span></div>
      </div>
      <div class="form-card form-card--crm">
        <h3>Do you have a CRM and if so what is it</h3>
        <div class="text-field text-field--wide">Type your CRM</div>
        <div class="btn-next">NEXT <svg viewBox="0 0 14 8" fill="none" stroke="currentColor" stroke-width="1.2"><path d="M0 4h12M9 1l3 3-3 3"/></svg></div>
      </div>
    </section>
    <div class="footer-cta">
      <div class="brand"><span class="brand-dot"></span><span class="brand-name">TALL PINE</span></div>
      <div class="footer-buttons"><span class="pill pill--call">CALL US (555) 014-2290</span><span class="pill pill--grow">GROW YOUR REVENUE</span></div>
    </div>
    <div class="footer-links">
      <div class="footer-col"><h4>QUICK LINKS</h4><ul><li>About</li><li>Industries</li><li>Training</li><li>Blog</li><li>Services</li><li>Contact</li></ul></div>
      <div class="footer-col"><h4>SERVICES</h4><ul><li>Programmatic Advertising</li><li>Search Engine Marketing (SEM)</li><li>Search Engine Optimization (SEO)</li><li>Content Marketing</li><li>Email Marketing</li><li>Paid Search Advertising</li><li>Paid Social Advertising</li></ul></div>
      <div class="footer-col"><h4>INDUSTRIES</h4><ul><li>Ecommerce</li><li>Electricians</li><li>Financial Services Marketing</li><li>Home Builders</li><li>Home Services</li><li>Hvac Companies</li><li>Cosmetic Surgery Centers</li><li>Dental Marketing</li><li>Education</li><li>Healthcare Medical Marketing</li><li>Plumbing Companies</li><li>Podiatrist Marketing</li><li>Landscapers</li></ul></div>
      <div class="footer-col"><h4>LINKS</h4><ul><li>Training</li><li>Resources</li><li>Privacy Policy</li><li>Sitemap</li><li>Terms Of Use</li><li>Press &amp; Media</li><li>Cookie Policy</li></ul></div>
    </div>
    <div class="footer-copy">© 2024 Company Name | All Rights Reserved</div>
  </article>

  <!-- ===== Step 5: personal information ===== -->
  <article class="page page--5">
    <header class="site-header">
      <div class="brand"><span class="brand-dot"></span><span class="brand-name">TALL PINE</span></div>
      <nav class="site-nav"><a>ABOUT</a><a>INDUSTRIES</a><a>SERVICES</a><a>BLOG</a><a>CONTACT US</a></nav>
      <div class="header-cta"><strong>GET A FREE CONSULTATION</strong><span>OR CAL US (555) 014-2290</span></div>
    </header>
    <section class="hero">
      <div class="hero-backdrop" role="img" aria-label="Dark abstract backdrop of a glowing network mesh wave"></div>
      <div class="hero-copy"><p class="hero-kicker">CONTACT US NOW</p><h1 class="hero-heading">GET A FREE ASSESMENTS</h1></div>
    </section>
    <section class="form-section">
      <div class="progress">
        <div class="progress-track"></div>
        <div class="progress-step"><span>STEP 1</span></div>
        <div class="progress-step"><span>STEP 2</span></div>
        <div class="progress-step"><span>STEP 3</span></div>
        <div class="progress-step"><span>STEP 4</span></div>
        <div class="progress-step is-active"><span>STEP 5</span></div>
      </div>
      <div class="form-card form-card--contact">
        <h3>What is your Personal Information</h3>
        <div class="contact-fields">
          <div class="text-field">Name</div>
          <div class="text-field">Email</div>
          <div class="text-field">Phone</div>
        </div>
        <div class="btn-next">SUBMIT <svg viewBox="0 0 14 8" fill="none" stroke="currentColor" stroke-width="1.2"><path d="M0 4h12M9 1l3 3-3 3"/></svg></div>
      </div>
    </section>
    <div class="footer-cta">
      <div class="brand"><span class="brand-dot"></span><span class="brand-name">TALL PINE</span></div>
      <div class="footer-buttons"><span class="pill pill--call">CALL US (555) 014-2290</span><span class="pill pill--grow">GROW YOUR REVENUE</span></div>
    </div>
    <div class="footer-links">
      <div class="footer-col"><h4>QUICK LINKS</h4><ul><li>About</li><li>Industries</li><li>Training</li><li>Blog</li><li>Services</li><li>Contact</li></ul></div>
      <div class="footer-col"><h4>SERVICES</h4><ul><li>Programmatic Advertising</li><li>Search Engine Marketing (SEM)</li><li>Search Engine Optimization (SEO)</li><li>Content Marketing</li><li>Email Marketing</li><li>Paid Search Advertising</li><li>Paid Social Advertising</li></ul></div>
      <div class="footer-col"><h4>INDUSTRIES</h4><ul><li>Ecommerce</li><li>Electricians</li><li>Financial Services Marketing</li><li>Home Builders</li><li>Home Services</li><li>Hvac Companies</li><li>Cosmetic Surgery Centers</li><li>Dental Marketing</li><li>Education</li><li>Healthcare Medical Marketing</li><li>Plumbing Companies</li><li>Podiatrist Marketing</li><li>Landscapers</li></ul></div>
      <div class="footer-col"><h4>LINKS</h4><ul><li>Training</li><li>Resources</li><li>Privacy Policy</li><li>Sitemap</li><li>Terms Of Use</li><li>Press &amp; Media</li><li>Cookie Policy</li></ul></div>
    </div>
    <div class="footer-copy">© 2024 Company Name | All Rights Reserved</div>
  </article>

</main>
</body>
</html>
```